Fernhale Business Card Design

We are looking for a fresh business card design for our new logo. We would like a business card that is unique but friendly. We are in the window coverings business offering blinds, shutters and shades for homes.

Target Market(s)

Targeting the end-consumer

Industry/Entity Type

Business

Requirements
Must have
• Must have a dedicates space for a photo of our sales person. Must contain our new logo (attached).

```html
<!DOCTYPE html>
<html lang="en">
<head>
<meta charset="utf-8">
<title>Fernhale Business Card</title>
<link rel="stylesheet" href="https://fonts.googleapis.com/css2?family=Roboto:wght@400;500&display=swap">
<style>
  :root {
    --backdrop: #e9e6e1;
    --paper: #f4f4f3;
    --panel-top: #6a6b6e;
    --panel-bottom: #7b7c80;
    --leaf: #80bc3c;
    --leaf-bright: #8cc63f;
    --ink-grey: #6c6d70;
    --white: #ffffff;
  }
  * { margin: 0; padding: 0; box-sizing: border-box; }
  html, body { width: 1200px; height: 960px; overflow: hidden; }
  body {
    background: var(--backdrop);
    font-family: "Roboto", Arial, sans-serif;
    position: relative;
  }
  .card {
    position: absolute;
    width: 600px;
    height: 343px;
    overflow: hidden;
    box-shadow: 0 2px 6px rgba(0,0,0,0.25);
  }
  /* Front */
  .card-front { left: 314px; top: 113px; background: var(--paper); }
  .front-brand {
    position: absolute; left: 40px; top: 146px;
    display: flex; align-items: center; gap: 10px;
  }
  .brand-square {
    width: 34px; height: 34px;
    border: 3px solid var(--ink-grey); border-radius: 4px;
  }
  .brand-name {
    font-size: 33px; font-weight: 400; color: var(--ink-grey); line-height: 1;
  }
  .contact-panel {
    position: absolute; left: 300px; top: 0; width: 300px; height: 343px;
    background: linear-gradient(180deg, var(--panel-top), var(--panel-bottom));
    border-top-left-radius: 72px;
    padding: 72px 0 0 36px;
    color: var(--white);
  }
  .person-name {
    font-size: 19px; font-weight: 500; color: var(--leaf-bright);
    text-transform: uppercase; line-height: 22px;
  }
  .person-role { font-size: 15px; font-weight: 500; line-height: 20px; }
  .address { margin-top: 11px; font-size: 14px; line-height: 19px; }
  .contact-list { list-style: none; margin-top: 9px; font-size: 14px; }
  .contact-list li { display: flex; align-items: center; height: 19px; gap: 9px; }
  .contact-list svg { width: 13px; height: 13px; fill: var(--leaf-bright); flex: none; }

  /* Back */
  .card-back { left: 311px; top: 472px; background: var(--leaf); }
  .portrait-slot {
    position: absolute; left: 0; top: 34px; width: 275px; height: 309px;
    background: linear-gradient(180deg, #f6f6f4, #eceeea);
  }
  .back-brand {
    position: absolute; left: 316px; top: 232px;
    display: flex; align-items: center; gap: 11px;
  }
  .back-brand .brand-square { width: 40px; height: 40px; border-color: var(--white); }
  .back-brand .brand-name { font-size: 38px; color: var(--white); }
  .back-url {
    position: absolute; left: 316px; top: 292px;
    font-size: 13px; letter-spacing: 5px; color: var(--white);
  }
</style>
</head>
<body>
  <section class="card card-front">
    <div class="front-brand">
      <span class="brand-square"></span>
      <span class="brand-name">Fernhale</span>
    </div>
    <div class="contact-panel">
      <p class="person-name">Daniel Hart</p>
      <p class="person-role">CEO/FOUNDER</p>
      <p class="address">2140 Alder Crest Road<br>Juneau, Alaska 34512</p>
      <ul class="contact-list">
        <li><svg viewBox="0 0 16 16"><path d="M3 1l3 0 1 4-2 1.5c1 2 2.5 3.5 4.5 4.5L11 9l4 1v3c0 1-1 2-2 2C7 15 1 9 1 3c0-1 1-2 2-2z"/></svg>555 210 4471</li>
        <li><svg viewBox="0 0 16 16"><path d="M4 0h8a1 1 0 0 1 1 1v14a1 1 0 0 1-1 1H4a1 1 0 0 1-1-1V1a1 1 0 0 1 1-1zm1 2v10h6V2z"/></svg>555 382 7190</li>
        <li><svg viewBox="0 0 16 16"><path d="M4 1h8v4H4zM1 6h14v7h-3v2H4v-2H1zm4 4v4h6v-4z"/></svg>555 604 2385</li>
        <li><svg viewBox="0 0 16 16"><path d="M1 3h14v10H1zm1.5 1.5L8 9l5.5-4.5z"/></svg>name@fernhale.com</li>
        <li><svg viewBox="0 0 16 16"><circle cx="8" cy="8" r="7"/></svg>www.fernhale.com</li>
      </ul>
    </div>
  </section>

  <section class="card card-back">
    <div class="portrait-slot" role="img" aria-label="Photo of the sales person, head and shoulders, in white silhouette"></div>
    <div class="back-brand">
      <span class="brand-square"></span>
      <span class="brand-name">Fernhale</span>
    </div>
    <p class="back-url">www.fernhale.com</p>
  </section>
</body>
</html>
```